BrindleStaffing Business Card Design

We are a staffing company finding positions for dedicated nurses and physicians.

Target Market(s)

Business Professionals

Industry/Entity Type

Staffing

Contact Information for Business Card

Gordon Pratley
Chairman
417 39th Avenue South
SAINT PETERSBURG FL 33712
813-555-4172 Mobile
813-555-8036 Fax
gpratley@brindlestaffing.com
www.brindlestaffing.com

Font styles to use
Sans Serif

Colors
fbee3e
f04a50
f37122

Requirements
Must have
• Logo Attached, see colors below. We'd like to see Yellow, Orange and Red.

```html
<!DOCTYPE html>
<html lang="en">
<head>
<meta charset="utf-8">
<title>BrindleStaffing Business Card</title>
<link rel="stylesheet" href="https://fonts.googleapis.com/css2?family=Rubik:wght@400;500;600&display=swap">
<style>
  :root {
    --backdrop: #3a3a3a;
    --card-black: #050505;
    --card-white: #ffffff;
    --ink: #1c1c1c;
    --accent-red: #f04a50;
    --accent-orange: #f37122;
    --accent-yellow: #fbb03b;
    --brand: #3a76c4;
  }
  * { box-sizing: border-box; margin: 0; padding: 0; }
  html, body {
    width: 1200px; height: 1000px; overflow: hidden;
    background: var(--backdrop);
    font-family: "Rubik", sans-serif;
  }
  .canvas { position: relative; width: 1200px; height: 1000px; }
  .card {
    position: absolute; left: 250px; width: 700px; height: 400px;
    box-shadow: 0 10px 28px rgba(0,0,0,.45);
  }
  .card--back {
    top: 70px; background: var(--card-black);
    display: flex; align-items: center; justify-content: center;
  }
  .card--back .wordmark { color: #fff; font-size: 46px; font-weight: 500; letter-spacing: .5px; }
  .card--front { top: 530px; background: var(--card-white); overflow: hidden; }
  .card--front .wordmark {
    position: absolute; left: 40px; top: 176px;
    color: var(--brand); font-size: 40px; font-weight: 500; letter-spacing: .3px;
  }
  .divider {
    position: absolute; left: 372px; top: 92px; width: 2px; height: 190px;
    background: var(--accent-yellow);
  }
  .contact { position: absolute; left: 396px; top: 94px; color: var(--ink); }
  .contact__name { color: var(--accent-orange); font-size: 21px; font-weight: 600; }
  .contact__title { font-size: 14px; margin-top: 6px; }
  .contact__address { font-size: 14px; line-height: 1.25; margin-top: 14px; }
  .contact__list { list-style: none; margin-top: 16px; font-size: 14px; }
  .contact__list li { display: flex; align-items: center; gap: 8px; line-height: 1.45; }
  .contact__list svg { width: 11px; height: 11px; fill: var(--accent-red); flex: none; }
  .contact__domain { color: var(--accent-orange); font-weight: 500; }
  .band {
    position: absolute; left: 0; right: 0; bottom: 0; height: 18px;
    background: var(--accent-red);
  }
</style>
</head>
<body>
<main class="canvas">
  <section class="card card--back" aria-label="Card back">
    <span class="wordmark">BrindleStaffing</span>
  </section>

  <section class="card card--front" aria-label="Card front">
    <span class="wordmark">BrindleStaffing</span>
    <div class="divider"></div>
    <div class="contact">
      <p class="contact__name">Gordon Pratley</p>
      <p class="contact__title">Chairman</p>
      <p class="contact__address">417 39th Avenue South<br>SAINT PETERSBURG FL 33712</p>
      <ul class="contact__list">
        <li><svg viewBox="0 0 12 12" aria-hidden="true"><path d="M2.5 1l2 2.2-1 1.3a7 7 0 0 0 4 4l1.3-1L11 9.5 9.7 11C5 11 1 7 1 2.3z"/></svg>813-555-4172</li>
        <li><svg viewBox="0 0 12 12" aria-hidden="true"><path d="M3 1h6v3H3zM1 5h10v5H9V8H3v2H1zM4 9h4v2H4z"/></svg>813-555-8036</li>
        <li><svg viewBox="0 0 12 12" aria-hidden="true"><path d="M1 2.5h10v7H1zM1.5 3l4.5 3.5L10.5 3v1L6 7.5 1.5 4z" fill-rule="evenodd"/></svg>gpratley@brindlestaffing.com</li>
        <li><svg viewBox="0 0 12 12" aria-hidden="true"><path d="M6 1a5 5 0 1 0 0 10A5 5 0 0 0 6 1zm0 1.2c.7.8 1.1 1.9 1.2 3.2H4.8C4.9 4.1 5.3 3 6 2.2zM2.2 6.6h1.6c.1 1.2.4 2.2.9 3A3.8 3.8 0 0 1 2.2 6.6zm0-1.2a3.8 3.8 0 0 1 2.5-3c-.5.8-.8 1.8-.9 3zm2.6 1.2h2.4C7.1 7.9 6.7 9 6 9.8 5.3 9 4.9 7.9 4.8 6.6zm3.4 0h1.6a3.8 3.8 0 0 1-2.5 3c.5-.8.8-1.8.9-3zm0-1.2c-.1-1.2-.4-2.2-.9-3a3.8 3.8 0 0 1 2.5 3z"/></svg>www.<span class="contact__domain">brindlestaffing</span>.com</li>
      </ul>
    </div>
    <div class="band"></div>
  </section>
</main>
</body>
</html>
```